Unique Builder wordpress website - Supply Graphics Only

We need a brand new website for a building company in Perth, Australia who constructs insulated panels (sip).
What is a SIP?
A SIP is a high-performance building panel used for floors, walls, and roofs in residential and commercial buildings. Panels are typically made using Expanded Polystyrene (EPS) sandwiched between two structural skins.
The design must incorporate a slick professional look and keep to the logo colours (Lime green & Blacks). The logo must not change colours or be altered. (
We will convert the graphics to a wordpress site. We have our own coders)
Design:
The website design must be clean, mobile friendly and the final design will be adapted to WordPress CMS.
The menus must contain dropdown menus and front page may contain a youtube video at a later date.
Fonts must be clear and easy to read
The contact us page will need to have an online form and google map.
The 16 pages listed will be the complete site and are for reference only. For this project the winning designer would need to supply the Homepage, and 1 inner pages only as PSD files.
The structure is as follows:
Home
About us
Marlow Fen Dwellings
What is a sip
Benefits
FAQ
Designs
Residential
Granny Flats
Architectural design
Photo Gallery <--- Would be great if a sample design can be provided
Services
Project management and custom design
Site Assembly
Kit Supply
Contact us
***We don't need the designer to design every page however a 1 inner page would be ideal****
Our Competitors websites
Note: the following websites look crap however, the following websites are some of our competitors. We want a clean and awesome layout.
http://www.corvamoda.com.au/
http://dralventorix.com.au/
http://www.quilbarrow.net.au/
New home builders and commercial builders
Building
5+ page

```html
<!DOCTYPE html>
<html lang="en">
<head>
<meta charset="utf-8">
<title>Verdant Panelworks – Advanced Building Technology</title>
<link rel="stylesheet" href="https://fonts.googleapis.com/css2?family=Montserrat:wght@400;700&family=Open+Sans:ital,wght@0,400;0,600;0,700;1,400&family=Questrial&display=swap">
<style>
:root{
  --lime:#9dc73a;
  --lime-dark:#86ad2c;
  --ink:#2b2b2b;
  --nav:#262626;
  --grey-bg:#efefef;
  --text:#555;
  --muted:#8a8a8a;
  --line:#d9d9d9;
  --white:#fff;
}
*{box-sizing:border-box;margin:0;padding:0}
html,body{width:1200px;height:3358px;overflow:hidden}
body{position:relative;background:var(--white);font-family:"Open Sans",sans-serif;color:var(--text)}
.abs{position:absolute}
.section-title{position:absolute;left:0;width:1200px;text-align:center;font-family:"Questrial",sans-serif;font-size:28px;color:var(--ink)}
.section-title b{font-family:"Montserrat",sans-serif;font-weight:700;font-size:25px}
.btn{position:absolute;height:34px;border-radius:17px;display:flex;align-items:center;padding:0 12px 0 22px;gap:14px;font-family:"Montserrat",sans-serif;font-weight:700;font-size:11px;color:var(--white);background:var(--ink);white-space:nowrap}
.btn .dot{width:20px;height:20px;border-radius:50%;background:var(--lime);display:flex;align-items:center;justify-content:center}
.btn--lime{background:var(--lime);color:var(--ink)}
.btn--lime .dot{background:var(--ink)}

/* header */
.brand{position:absolute;left:90px;top:30px;display:flex;align-items:center;gap:14px}
.brand__mark{width:40px;height:40px;background:var(--lime)}
.brand__name{font-family:"Montserrat",sans-serif;font-weight:700;font-size:30px;color:var(--lime);white-space:nowrap}
.brand__tag{position:absolute;left:144px;top:82px;font-family:"Montserrat",sans-serif;font-size:9px;letter-spacing:1px;color:var(--ink)}
.pill{position:absolute;top:38px;height:36px;border-radius:18px;background:#f2f2f2;border:1px solid #ddd;display:flex;align-items:center;gap:10px;padding:0 14px 0 6px;font-family:"Montserrat",sans-serif;font-weight:700;font-size:13px;color:var(--ink);white-space:nowrap}
.pill .ic{width:26px;height:26px;border-radius:13px;background:var(--lime);display:flex;align-items:center;justify-content:center}
.nav{position:absolute;left:0;top:112px;width:1200px;height:49px;background:var(--nav);display:flex;justify-content:space-between;align-items:center;padding:0 90px 0 100px;font-family:"Montserrat",sans-serif;font-weight:700;font-size:12px;color:var(--white);text-transform:uppercase;white-space:nowrap}
.nav .active{color:var(--lime)}

/* hero */
.hero{position:absolute;left:0;top:161px;width:1200px;height:522px;background:linear-gradient(120deg,#3d4a36 0%,#6f7d58 40%,#8fa07c 60%,#5e6a4a 100%)}
.hero__panel{position:absolute;left:0;top:0;width:600px;height:522px;background:rgba(20,20,20,.55)}
.hero__title{position:absolute;left:0;width:600px;top:128px;text-align:center;font-family:"Montserrat",sans-serif;font-weight:700;font-size:44px;color:var(--lime);white-space:nowrap}
.hero__text{position:absolute;left:100px;width:450px;top:212px;text-align:center;font-size:20px;line-height:32px;color:var(--white)}
.arrow-circle{position:absolute;width:36px;height:36px;border-radius:50%;background:rgba(255,255,255,.9);display:flex;align-items:center;justify-content:center}

/* about */
.about__title{position:absolute;left:146px;top:710px;font-family:"Questrial",sans-serif;font-size:28px;color:var(--ink);white-space:nowrap}
.about__title b{font-family:"Montserrat",sans-serif}
.about__text{position:absolute;left:90px;top:758px;width:622px;font-size:15px;line-height:21.5px}
.video{position:absolute;left:732px;top:712px;width:358px;height:273px;border:4px solid #e6e6e6;background:linear-gradient(160deg,#6b4b2e,#b58a5a 45%,#cfb08a 70%,#7a8fa2)}
.video__bar{position:absolute;left:0;bottom:0;width:100%;height:42px;background:#1e1e1e;display:flex;align-items:center;gap:14px;padding:0 14px;color:var(--white);font-size:13px;font-weight:600}
.video__track{flex:1;height:6px;border-radius:3px;background:#555;position:relative}
.video__track i{position:absolute;left:0;top:0;width:40%;height:6px;border-radius:3px;background:#aaa}
.video__play{position:absolute;left:146px;top:80px;width:66px;height:66px;border-radius:50%;background:rgba(255,255,255,.85);display:flex;align-items:center;justify-content:center}

/* benefits */
.benefits{position:absolute;left:0;top:1012px;width:1200px;height:656px;background:var(--grey-bg)}
.benefit{position:absolute;width:336px}
.benefit h3{font-family:"Montserrat",sans-serif;font-weight:700;font-size:15px;line-height:20px;color:var(--ink);text-transform:uppercase;margin-bottom:6px}
.benefit p{font-size:11.5px;line-height:17px;color:var(--muted)}
.b-icon{position:absolute;width:116px;height:116px;border-radius:50%;background:var(--lime);border:6px solid #555;display:flex;align-items:center;justify-content:center}

/* projects */
.project{position:absolute;width:300px;text-align:center}
.project__img{width:100%;height:168px;border:4px solid #f0f0f0}
.project h4{margin-top:26px;font-family:"Montserrat",sans-serif;font-weight:700;font-size:16px;color:var(--ink)}
.project p{margin-top:10px;font-size:12.5px;line-height:18px;color:var(--text);padding:0 6px}
.chev{position:absolute;width:20px;height:40px}

/* stories */
.stories{position:absolute;left:0;top:2120px;width:1200px;height:325px;background:var(--lime)}
.story{position:absolute;top:137px;height:143px;background:var(--white);padding:48px 22px 0;text-align:center}
.story h5{font-family:"Open Sans",sans-serif;font-weight:700;font-size:12px;color:var(--ink);margin-bottom:8px}
.story p{font-style:italic;font-size:11px;line-height:16px;color:var(--text);text-align:left}
.avatar{position:absolute;top:-46px;left:50%;margin-left:-34px;width:68px;height:68px;border-radius:50%;background:linear-gradient(#cfcfcf,#9a9a9a);border:4px solid var(--white)}

/* clients */
.client{position:absolute;top:2552px;width:177px;height:63px;background:var(--white);border:1px solid var(--line);display:flex;align-items:center;justify-content:center;font-family:"Montserrat",sans-serif;font-weight:700;font-size:22px;color:#6d6d6d}
.client-row-bg{position:absolute;left:0;top:2445px;width:1200px;height:224px;background:#f5f5f5}
.small-arrow{position:absolute;top:2574px;width:20px;height:20px;border-radius:50%;background:#d6d6d6;display:flex;align-items:center;justify-content:center}

/* map */
.map{position:absolute;left:0;top:2669px;width:1200px;height:268px;background:linear-gradient(135deg,#e9e6df,#dcdad3 50%,#e5e2da)}

/* contact */
.contact{position:absolute;left:0;top:2937px;width:1200px;height:359px;background:linear-gradient(#f4f4f4,#e8e8e8)}
.field{position:absolute;background:var(--white);border:1px solid #d3d3d3;font-size:11px;color:#777;padding:10px 12px;white-space:nowrap}
.send{position:absolute;left:365px;top:3209px;width:334px;height:36px;background:var(--ink);color:var(--lime);font-family:"Montserrat",sans-serif;font-weight:700;font-size:14px;display:flex;align-items:center;justify-content:center}
.info{position:absolute;left:806px}
.info .ic{position:absolute;left:0;top:0;width:24px;height:24px;border-radius:50%;background:var(--lime);display:flex;align-items:center;justify-content:center}
.info h6{position:absolute;left:40px;top:0;font-family:"Open Sans",sans-serif;font-weight:600;font-size:16px;color:var(--ink);white-space:nowrap}
.info p{position:absolute;left:40px;top:26px;font-size:13px;line-height:19px;color:var(--muted);white-space:nowrap}
.footer{position:absolute;left:0;top:3296px;width:1200px;height:62px;background:var(--nav);color:#ddd;font-size:13px;display:flex;align-items:center;justify-content:center}
</style>
</head>
<body>

<header>
  <div class="brand"><span class="brand__mark"></span><span class="brand__name">Verdant Panelworks</span></div>
  <div class="brand__tag">ADVANCED BUILDING TECHNOLOGY</div>
  <div class="pill" style="left:726px"><span class="ic"><svg width="14" height="14" viewBox="0 0 24 24"><path d="M6 2l4 4-2 3c1 3 4 6 7 7l3-2 4 4-3 4C10 22 2 14 2 5z" fill="#fff"/></svg></span>123-456-7890</div>
  <div class="pill" style="left:886px"><span class="ic"><svg width="14" height="14" viewBox="0 0 24 24"><rect x="2" y="5" width="20" height="14" fill="#fff"/><path d="M2 5l10 8 10-8" stroke="#9dc73a" stroke-width="2" fill="none"/></svg></span>info@verdantpanelworks.com</div>
  <nav class="nav">
    <span class="active">Home</span><span>About Us</span><span>Marlow Fen Dwellings</span><span>What is a SIP</span><span>Benefits</span><span>FAQs</span><span>Designs ▾</span><span>Services ▾</span><span>Contact Us</span>
  </nav>
</header>

<section class="hero" role="img" aria-label="Photo of a green weatherboard home with white windows and timber stairs">
  <div class="hero__panel"></div>
  <div class="hero__title">Verdant Panelworks</div>
  <p class="hero__text">We specialize in supplying on time and on budget, with high quality structural kits to builders and developers specific to their needs or requirements.</p>
  <div class="btn btn--lime" style="left:257px;top:368px">READ MORE <span class="dot"><svg width="8" height="10"><path d="M1 1l6 4-6 4z" fill="#9dc73a"/></svg></span></div>
  <div class="arrow-circle" style="left:28px;top:240px"><svg width="10" height="12"><path d="M9 1L2 6l7 5z" fill="#333"/></svg></div>
  <div class="arrow-circle" style="left:1136px;top:240px"><svg width="10" height="12"><path d="M1 1l7 5-7 5z" fill="#333"/></svg></div>
</section>

<section class="about">
  <h2 class="about__title">About <b>Verdant Panelworks</b></h2>
  <p class="about__text">Lorem ipsum dolor sit amet, consectetur adipiscing elit. Vivamus id leo quis lectus fringilla viverra. Vestibulum dictum consectetur turpis id tempus. Nullam venenatis, justo eget gravida rutrum, purus sapien porttitor ex, at rhoncus urna arcu sit amet arcu. Duis ut metus felis. Aliquam eget nulla vestibulum, ultricies nulla quis, tincidunt mauris. Lorem ipsum dolor sit amet, consectetur adipiscing elit. Vivamus id leo quis lectus fringilla viverra. Vestibulum dictum consectetur turpis id tempus. Nullam venenatis, justo eget gravida rutrum, purus sapien porttitor ex.</p>
  <div class="btn" style="left:90px;top:946px">READ MORE <span class="dot"><svg width="8" height="10"><path d="M1 1l6 4-6 4z" fill="#2b2b2b"/></svg></span></div>
  <div class="video" role="img" aria-label="Video still of a builder fixing timber roof trusses">
    <div class="video__play"><svg width="24" height="28"><path d="M2 1l21 13L2 27z" fill="#333"/></svg></div>
    <div class="video__bar"><svg width="12" height="14"><path d="M1 1l10 6-10 6z" fill="#fff"/></svg><span>04:59</span><span class="video__track"><i></i></span><span>10:35</span><svg width="16" height="14"><path d="M1 5h4l5-4v12l-5-4H1z" fill="#fff"/><path d="M12 4q3 3 0 6" stroke="#fff" fill="none"/></svg></div>
  </div>
</section>

<section class="benefits">
  <h2 class="section-title" style="top:38px">Our <b>Benefits</b></h2>
  <div class="benefit" style="left:100px;top:124px"><h3>Suitable for both residential and commercial buildings</h3><p>Lorem ipsum dolor sit amet, consectetuer adipiscing elit, sed diam nonummy nibh euismod tincidunt ut laoreetfgf dolore magna aliquam erat volutpat.</p></div>
  <div class="benefit" style="left:772px;top:124px"><h3>20 + Year history of performance in cyclonic locations in WA</h3><p>Lorem ipsum dolor sit amet, consectetuer adipiscing elit, sed diam nonummy nibh euismod tincidunt ut laoreetfgf dolore magna aliquam erat volutpat.</p></div>
  <div class="benefit" style="left:100px;top:306px"><h3>High level of captive insulation</h3><p>Lorem ipsum dolor sit amet, consectetuer adipiscing elit, sed diam nonummy nibh euismod tincidunt ut laoreetfgf dolore magna aliquam erat volutpat.</p></div>
  <div class="benefit" style="left:772px;top:306px"><h3>Reduced build time</h3><p>Lorem ipsum dolor sit amet, consectetuer adipiscing elit, sed diam nonummy nibh euismod tincidunt ut laoreetfgf dolore magna aliquam erat volutpat.</p></div>
  <div class="benefit" style="left:100px;top:490px"><h3>Very strong, light weight and durable</h3><p>Lorem ipsum dolor sit amet, consectetuer adipiscing elit, sed diam nonummy nibh euismod tincidunt ut laoreetfgf dolore magna aliquam erat volutpat.</p></div>
  <div class="benefit" style="left:772px;top:490px"><h3>Energy efficient</h3><p>Lorem ipsum dolor sit amet, consectetuer adipiscing elit, sed diam nonummy nibh euismod tincidunt ut laoreetfgf dolore magna aliquam erat volutpat.</p></div>

  <div class="b-icon" style="left:464px;top:123px"><svg width="54" height="54" viewBox="0 0 54 54" fill="none" stroke="#fff" stroke-width="3"><rect x="8" y="10" width="24" height="38"/><rect x="32" y="22" width="14" height="26"/><path d="M14 18h4M22 18h4M14 26h4M22 26h4M14 34h4M22 34h4M37 30h4M37 38h4"/></svg></div>
  <div class="b-icon" style="left:618px;top:123px"><svg width="54" height="54" viewBox="0 0 54 54" fill="none" stroke="#fff" stroke-width="3"><path d="M6 10h42M10 18h34M15 26h24M19 34h16M23 42h8"/></svg></div>
  <div class="b-icon" style="left:464px;top:307px"><svg width="54" height="54" viewBox="0 0 54 54" fill="none" stroke="#fff" stroke-width="3"><path d="M5 27L27 8l22 19M11 22v24h32V22"/><path d="M21 46V33h12v13"/></svg></div>
  <div class="b-icon" style="left:618px;top:307px"><svg width="54" height="54" viewBox="0 0 54 54" fill="none" stroke="#fff" stroke-width="3"><circle cx="27" cy="30" r="17"/><path d="M27 30V19M22 6h10M27 6v7M41 13l4-4"/></svg></div>
  <div class="b-icon" style="left:464px;top:491px"><svg width="54" height="54" viewBox="0 0 54 54" fill="none" stroke="#fff" stroke-width="4"><rect x="6" y="22" width="26" height="12" rx="6" transform="rotate(-45 19 28)"/><rect x="22" y="20" width="26" height="12" rx="6" transform="rotate(-45 35 26)"/></svg></div>
  <div class="b-icon" style="left:618px;top:491px"><svg width="54" height="54" viewBox="0 0 54 54" fill="none" stroke="#fff" stroke-width="3"><path d="M18 36c-5-4-7-8-7-13a16 16 0 0132 0c0 5-2 9-7 13v5H18z"/><path d="M20 46h14M29 16l-5 9h7l-5 9"/></svg></div>
</section>

<section class="projects">
  <h2 class="section-title" style="top:1690px">Recent <b>Projects</b></h2>
  <svg class="chev" style="left:46px;top:1827px" viewBox="0 0 20 40"><path d="M18 2L3 20l15 18" stroke="#bbb" stroke-width="2" fill="none"/></svg>
  <svg class="chev" style="left:1134px;top:1827px" viewBox="0 0 20 40"><path d="M2 2l15 18L2 38" stroke="#bbb" stroke-width="2" fill="none"/></svg>
  <div class="project" style="left:113px;top:1762px">
    <div class="project__img" role="img" aria-label="Photo of a two-storey panel home under construction" style="background:linear-gradient(#b9cfe3,#a98b66 60%,#7d6448)"></div>
    <h4>Lorem Ipsum</h4><p>Lorem ipsum dolor sit amet. consectetuer in the adipiscing elit, sed diam nonummy nibhers and euismod tincidunt ut laoreet dolore magna.</p>
  </div>
  <div class="project" style="left:450px;top:1762px">
    <div class="project__img" role="img" aria-label="Photo of timber wall framing and panels on a building site" style="background:linear-gradient(#9fb6c8,#c59b66 50%,#8b6a45)"></div>
    <h4>Lorem Ipsum</h4><p>Lorem ipsum dolor sit amet. consectetuer in the adipiscing elit, sed diam nonummy nibhers and euismod tincidunt ut laoreet dolore magna.</p>
  </div>
  <div class="project" style="left:780px;top:1762px">
    <div class="project__img" role="img" aria-label="Photo of stacked insulated panel samples with foam cores" style="background:linear-gradient(#d9b27a,#f0ece4 50%,#c89b62)"></div>
    <h4>Lorem Ipsum</h4><p>Lorem ipsum dolor sit amet. consectetuer in the adipiscing elit, sed diam nonummy nibhers and euismod tincidunt ut laoreet dolore magna.</p>
  </div>
  <div class="btn" style="left:196px;top:2056px">READ MORE <span class="dot"><svg width="8" height="10"><path d="M1 1l6 4-6 4z" fill="#2b2b2b"/></svg></span></div>
  <div class="btn" style="left:531px;top:2056px">READ MORE <span class="dot"><svg width="8" height="10"><path d="M1 1l6 4-6 4z" fill="#2b2b2b"/></svg></span></div>
  <div class="btn" style="left:861px;top:2056px">READ MORE <span class="dot"><svg width="8" height="10"><path d="M1 1l6 4-6 4z" fill="#2b2b2b"/></svg></span></div>
</section>

<section class="stories">
  <h2 class="section-title" style="top:18px">Success <b>Stories</b></h2>
  <div class="story" style="left:123px;width:314px"><div class="avatar" role="img" aria-label="Client portrait"></div><h5>Lorem ipsum dolor</h5><p>“ Lorem ipsum dolor sit amet, ffg jrdkvjbnjg consectetuer adipiscing elit, sed diamgnj. nonummy nibh euismod tincidunt utfgh elit. laoreet dolore magna aliquam erattgh. ”</p></div>
  <div class="story" style="left:459px;width:284px"><div class="avatar" role="img" aria-label="Client portrait"></div><h5>Lorem ipsum dolor</h5><p>“ Lorem ipsum dolor sit amet, ffg jrdkvjbnjg consectetuer adipiscing elit, sed diamgnj. nonummy nibh euismod tincidunt utfgh elit. laoreet dolore magna aliquam erattgh. ”</p></div>
  <div class="story" style="left:790px;width:289px"><div class="avatar" role="img" aria-label="Client portrait"></div><h5>Lorem ipsum dolor</h5><p>“ Lorem ipsum dolor sit amet, ffg jrdkvjbnjg consectetuer adipiscing elit, sed diamgnj. nonummy nibh euismod tincidunt utfgh elit. laoreet dolore magna aliquam erattgh. ”</p></div>
</section>

<section class="clients">
  <div class="client-row-bg"></div>
  <h2 class="section-title" style="top:2466px">Our <b>Clients</b></h2>
  <span class="small-arrow" style="left:42px"><svg width="6" height="8"><path d="M5 0L0 4l5 4z" fill="#fff"/></svg></span>
  <span class="small-arrow" style="left:1138px"><svg width="6" height="8"><path d="M1 0l5 4-5 4z" fill="#fff"/></svg></span>
  <div class="client" style="left:90px">Tidewell</div>
  <div class="client" style="left:302px">NORVANE</div>
  <div class="client" style="left:510px">Brightmoor</div>
  <div class="client" style="left:721px">Kestrel</div>
  <div class="client" style="left:929px">Ostravo</div>
</section>

<div class="map" role="img" aria-label="Street map showing the office location"></div>
<svg class="abs" style="left:570px;top:2780px" width="60" height="60" viewBox="0 0 60 60"><rect x="12" y="12" width="36" height="36" transform="rotate(45 30 30)" fill="#fff" stroke="#555" stroke-width="3"/></svg>

<section class="contact">
  <h2 class="section-title" style="top:30px">Contact <b>Us</b></h2>
  <div class="abs" style="left:90px;top:104px;font-size:17px;color:var(--ink)">Quick Inquiry</div>
  <div class="field" style="left:90px;top:162px;width:250px;height:36px">Your Email</div>
  <div class="field" style="left:90px;top:220px;width:250px;height:36px">Apply with your profile URL</div>
  <div class="field" style="left:90px;top:272px;width:250px;height:36px">Or upload your CV</div>
  <div class="abs" style="left:304px;top:272px;width:36px;height:36px;background:var(--lime);display:flex;align-items:center;justify-content:center"><svg width="16" height="16" viewBox="0 0 16 16"><path d="M8 1v10M4 5l4-4 4 4M2 14h12" stroke="#fff" stroke-width="2" fill="none"/></svg></div>
  <div class="field" style="left:365px;top:162px;width:334px;height:92px">How We Can Help You?</div>
  <div class="abs" style="left:746px;top:100px;width:1px;height:230px;background:#cfcfcf"></div>
  <div class="info" style="top:113px"><span class="ic"><svg width="10" height="14" viewBox="0 0 10 14"><path d="M5 0a5 5 0 015 5c0 4-5 9-5 9S0 9 0 5a5 5 0 015-5z" fill="#fff"/></svg></span><h6>Address Information</h6><p>Lorem Ipsum Dolor Sit<br>Amet Adipcing Elit - 123456</p></div>
  <div class="info" style="top:204px"><span class="ic"><svg width="12" height="10"><rect width="12" height="10" fill="#fff"/><path d="M0 0l6 5 6-5" stroke="#9dc73a" fill="none"/></svg></span><h6>Email</h6><p>info@verdantpanelworks.com</p></div>
  <div class="info" style="top:276px"><span class="ic"><svg width="12" height="12" viewBox="0 0 24 24"><path d="M6 2l4 4-2 3c1 3 4 6 7 7l3-2 4 4-3 4C10 22 2 14 2 5z" fill="#fff"/></svg></span><h6>Call Us</h6><p>123-456-7890</p></div>
</section>
<div class="send">Send Us Your Information</div>

<footer class="footer">Copyright © 2016 Verdant Panelworks . All Rights Reserved.</footer>

</body>
</html>
```